Im want a website LIKE VRX's and FleetHollow.com's with product payment options like Trenzo's

I need a website LIKE VRX with a header made EXACTLY LIKE THAT OF FLEETHOLLOWS .

The front page photo should be like that of FLEETHOLLOW's webpage as well.

The name of the website will be called "M.K. (Caldera Key)".

We will be targeting ALL MARKETS in a small town in central Panama and charging businesses "listing fees" like a phone book does but also providing informational blogs, news, and other interesting activities.

THIS IS A MULTI PAGE WEBSITE

THIS IS WHERE VRX's website meets Brivelle/FleetHollow.

Once the layout is built I will tweak and modify, add information, and upload items for sale.

Here is a list of specific categories that should be listed out above the front page header image/search bar

-- Home -- News -- Travel -- Activities -- Shop & Dine -- Store -- More... --

These categories should be spread across the bottom of the page in three sections:

WHATS SO GREAT ABOUT (Caldera Key),
HAND PICKED TOURS
ACTIVITIES etc.

Also lets use www.Trenzo.example 's
"HOT DESTINATIONS"
"BEAT THE BEST PRICES IN BOQUETE"
"OCTOBERS INSIDER PICKS"
"TOP DESTINATIONS"
and spread them in four sections side-by-side near the bottom of the page.

Overall I would like to see the finished product to be something LIKE VRX's and FleetHollows.

WE NEED ONLINE PAYMENT OPTIONS LIKE BRIVELLE'S WEBSITE HAS

This will be a desktop website but should be very mobile friendly as well.

-rodmund

P.S. Good luck!

If it isn't already too late to change the website name, the name of the website should be "Caldera Key". Added Friday, October 9, 2015

What do you guys think the budget should be to win this? Added Saturday, October 10, 2015

www.palmorra.example is the most amazing simple site. Whoever can make me a replica with my specifications will win immediately!!!! Added Sunday, October 18, 2015

OMG www.palmorra.example is the bomb!So simple and elegant. Whoever can make me an EXACT REPLICA OF WWW.PALMORRA.EXAMPLE as my site with the specifications mentioned in my brief will take home the $825.00 immediately! Good luck amigos! Added Sunday, October 18, 2015

Does anybody know how to add recurring monthly billing options on this website? Added Sunday, October 18, 2015

ALL MARKETS

Product

Coded - Design and coding required

5+ page

• Coinvey payment options.
• I must be able to add and remove photos/text and video from the HTML files in the page.
• Be creative my friends, and may the odds be forever in your favor!
• I added some photos of a good layout for our page below.

```html
<!DOCTYPE html>
<html lang="en">
<head>
<meta charset="utf-8">
<title>Caldera Key</title>
<link href="https://fonts.googleapis.com/css2?family=Open+Sans:wght@400;600;700&display=swap" rel="stylesheet">
<style>
:root{
  --blue:#2a9ad6;
  --blue-dark:#1d7fb8;
  --ink:#333a40;
  --muted:#777f86;
  --header:#17222d;
  --footer:#1c1f22;
  --light:#f2f3f4;
  --white:#ffffff;
  --star:#2a9ad6;
}
*{margin:0;padding:0;box-sizing:border-box}
html,body{width:714px;height:1200px;overflow:hidden}
body{font-family:"Open Sans",Arial,sans-serif;color:var(--ink);background:var(--white);position:relative}
.abs{position:absolute}

/* top scenery */
.scenery{left:0;top:0;width:714px;height:420px;background:linear-gradient(180deg,#3b6e94 0%,#6ea4c6 35%,#a9c9d8 70%,#d9e3e3 100%)}
.site-header{left:0;top:0;width:714px;height:52px;background:rgba(17,28,40,.92)}
.brand{left:22px;top:15px;color:var(--white);font-size:17px;font-weight:700;letter-spacing:.5px}
.lang{left:536px;top:20px;font-size:7px;color:#c9d2da}
.lang-box{left:570px;top:18px;width:34px;height:12px;background:#2b3a48;border:1px solid #4d5e6d}
.social-top{top:17px;width:13px;height:13px;border-radius:50%}
.nav{left:0;top:52px;width:714px;height:31px;background:var(--blue)}
.nav ul{list-style:none;display:flex;position:absolute;left:70px;top:0;height:31px}
.nav li{font-size:7.5px;font-weight:600;color:var(--white);width:82px;text-align:center;line-height:31px}
.nav li.active{background:var(--blue-dark)}

/* hero */
.hero{left:60px;top:96px;width:595px;height:284px;background:linear-gradient(180deg,#f0a23a 0%,#f6c55a 30%,#d27a2e 62%,#5a3a26 100%)}
.hero h1{position:absolute;left:0;width:100%;top:70px;text-align:center;color:var(--white);font-size:29px;font-weight:700;letter-spacing:.5px}
.hero p{position:absolute;left:130px;width:335px;top:116px;text-align:center;color:var(--white);font-size:8px;line-height:13px}
.btn{position:absolute;left:262px;top:176px;width:70px;height:22px;background:var(--blue);color:var(--white);font-size:8px;font-weight:700;text-align:center;line-height:22px}
.dots{position:absolute;left:280px;top:257px;display:flex;gap:5px}
.dots span{width:6px;height:6px;border-radius:50%;border:1px solid var(--white)}
.dots span.on{background:var(--white)}

/* features */
.section-title{left:0;width:714px;text-align:center;font-size:16px;font-weight:400;color:var(--blue);letter-spacing:.5px}
.section-title b{font-weight:400;color:var(--ink)}
.rule{left:337px;width:40px;height:2px;background:var(--blue)}
.intro{left:90px;top:488px;width:534px;text-align:center;font-size:7px;line-height:11px;color:var(--muted)}
.feature{top:560px;width:175px}
.feature svg{position:absolute;left:0;top:0}
.feature h3{position:absolute;left:26px;top:2px;font-size:8px;font-weight:600;color:var(--blue)}
.feature h3.plain{color:var(--ink)}
.feature p{position:absolute;left:26px;top:18px;width:145px;font-size:6.5px;line-height:10px;color:var(--muted)}
.feature .more{position:absolute;left:26px;top:64px;font-size:6.5px;color:var(--blue)}

/* listings */
.listings{left:0;top:665px;width:714px;height:262px;background:var(--light)}
.card{top:738px;width:138px}
.card .photo{width:138px;height:95px}
.card h4{margin-top:10px;font-size:7px;font-weight:600;color:var(--blue)}
.card p{margin-top:4px;font-size:6.5px;line-height:10px;color:var(--muted)}
.card .stars{margin-top:4px;display:flex;gap:2px}

/* feedback */
.quote{left:95px;top:980px;width:524px;text-align:center;font-size:7px;line-height:11px;color:var(--muted)}
.avatar{left:337px;top:1025px;width:40px;height:40px;border-radius:50%;background:linear-gradient(180deg,#c9cfd6,#8e99a4)}
.reviewer{left:0;width:714px;top:1074px;text-align:center;font-size:7px;font-weight:700;color:var(--blue)}

/* footer */
.site-footer{left:0;top:1145px;width:714px;height:55px;background:var(--footer)}
.footer-links{left:60px;top:1160px;display:flex;gap:14px;font-size:7px;color:var(--white);font-weight:600}
.copyright{left:60px;top:1177px;font-size:6px;color:#8b9299}
.connect{left:462px;top:1166px;font-size:7px;font-weight:700;color:var(--white)}
.social{top:1162px;width:15px;height:15px;border-radius:50%}
</style>
</head>
<body>

<div class="abs scenery" role="img" aria-label="Tropical beach with palm trees and blue sky"></div>

<header class="abs site-header"></header>
<div class="abs brand">CALDERA KEY</div>
<div class="abs lang">Language</div>
<div class="abs lang-box"></div>
<span class="abs social-top" style="left:612px;background:#3b5998"></span>
<span class="abs social-top" style="left:628px;background:#29a9e1"></span>
<span class="abs social-top" style="left:644px;background:#dd4b39"></span>
<span class="abs social-top" style="left:660px;background:#cb2027"></span>

<nav class="abs nav">
  <ul>
    <li class="active">HOME</li>
    <li>ABOUT US</li>
    <li>SERVICES</li>
    <li>BLOG</li>
    <li>CONTACT US</li>
    <li>LOGIN</li>
    <li>REGISTER</li>
  </ul>
</nav>

<section class="abs hero" role="img" aria-label="Two hikers with backpacks watching a golden sunset over the mountains">
  <h1>AT VERO EOS ET ACCUSAMUS</h1>
  <p>Discover quiet beaches, cloud forest trails and friendly local hosts across the island. Book guided trips and stays in a few simple steps.</p>
  <div class="btn">READ MORE</div>
  <div class="dots"><span class="on"></span><span></span><span></span><span></span></div>
</section>

<h2 class="abs section-title" style="top:438px">CALDERA KEY <b>FEATURES</b></h2>
<div class="abs rule" style="top:464px"></div>
<p class="abs intro">Caldera Key brings together local businesses, guides and hosts in one easy directory. Browse tours, hotels and rentals, read fresh news from town and find the best ways to spend your days in the highlands of central Panama, all in one place.</p>

<div class="abs feature" style="left:60px">
  <svg width="16" height="16" viewBox="0 0 16 16"><path d="M1 9 L15 2 L11 14 L8 10 Z" fill="#2a9ad6"/></svg>
  <h3>SELLING GUIDED TOURS</h3>
  <p>Walk the trails with local guides who know every river, coffee farm and lookout point in the area.</p>
  <span class="more">Read More »</span>
</div>
<div class="abs feature" style="left:283px">
  <svg width="16" height="16" viewBox="0 0 16 16"><rect x="1" y="3" width="14" height="2" fill="#555"/><rect x="1" y="7" width="14" height="2" fill="#555"/><rect x="1" y="11" width="14" height="2" fill="#555"/></svg>
  <h3 class="plain">HOTEL/HOSTELS</h3>
  <p>Compare small hotels and friendly hostels near town, check rates and book your room in minutes.</p>
  <span class="more">Read More »</span>
</div>
<div class="abs feature" style="left:470px">
  <svg width="16" height="16" viewBox="0 0 16 16"><circle cx="6" cy="8" r="4" fill="none" stroke="#555" stroke-width="2.5"/><circle cx="12.5" cy="4" r="2.5" fill="none" stroke="#555" stroke-width="1.8"/></svg>
  <h3 class="plain">RENTAL VEHICLES</h3>
  <p>Find cars, scooters and bikes for rent from trusted shops so you can explore at your own pace.</p>
  <span class="more">Read More »</span>
</div>

<section class="abs listings"></section>
<h2 class="abs section-title" style="top:685px">OUR <b style="color:var(--blue)">LISTINGS</b></h2>
<div class="abs rule" style="top:711px"></div>

<div class="abs card" style="left:60px">
  <div class="photo" role="img" aria-label="Boats on a turquoise bay" style="background:linear-gradient(180deg,#7fc0e6,#3a8fb8 60%,#2c6d86)"></div>
  <h4>NEW LISTING</h4>
  <p>Simply a short note about this place and what it offers.</p>
  <div class="stars">★★★★★</div>
</div>
<div class="abs card" style="left:212px">
  <div class="photo" role="img" aria-label="Traveller on a pier over calm water" style="background:linear-gradient(180deg,#bcdcef,#6aa8cc 60%,#42708a)"></div>
  <h4>NEW LISTING</h4>
  <p>Simply a short note about this place and what it offers.</p>
  <div class="stars">★★★★★</div>
</div>
<div class="abs card" style="left:364px">
  <div class="photo" role="img" aria-label="Group of friends on holiday" style="background:linear-gradient(180deg,#d8cfc2,#b59a82 60%,#7d6a5b)"></div>
  <h4>NEW LISTING</h4>
  <p>Simply a short note about this place and what it offers.</p>
  <div class="stars">★★★★★</div>
</div>
<div class="abs card" style="left:516px">
  <div class="photo" role="img" aria-label="Boat on a green lagoon between cliffs" style="background:linear-gradient(180deg,#9fd0e0,#5aa7a0 55%,#3f7a5e)"></div>
  <h4>NEW LISTING</h4>
  <p>Simply a short note about this place and what it offers.</p>
  <div class="stars">★★★★★</div>
</div>

<h2 class="abs section-title" style="top:940px">CUSTOMER <b style="color:var(--blue)">FEEDBACK</b></h2>
<div class="abs rule" style="top:966px"></div>
<p class="abs quote">The team made it easy to find a guide, a room and a car for our week in the highlands. Everything was clear, prices were fair and the local tips helped us see places we would never have found on our own.</p>
<div class="abs avatar" role="img" aria-label="Portrait of the reviewer"></div>
<div class="abs reviewer">THEO MARLIN</div>

<footer class="abs site-footer"></footer>
<div class="abs footer-links"><span>HOME</span><span>ABOUT US</span><span>SERVICES</span><span>BLOG</span><span>CONTACT US</span></div>
<div class="abs copyright">Copyright © 2015 Caldera Key. All Rights Reserved.</div>
<div class="abs connect">CONNECT US</div>
<span class="abs social" style="left:536px;background:#3b5998"></span>
<span class="abs social" style="left:556px;background:#29a9e1"></span>
<span class="abs social" style="left:576px;background:#dd4b39"></span>
<span class="abs social" style="left:596px;background:#e4803a"></span>
<span class="abs social" style="left:616px;background:#cb2027"></span>
<span class="abs social" style="left:636px;background:#007bb6"></span>

</body>
</html>
```